Spring Detox sale graphics for social media

You MUST read the Brief in the WORD document and follow the instructions there. I want to create 10 social media graphics (new Instagram size 4:5 (1080 x 1350 pixels) focusing on our Mother’s Day Spring Detox Sale graphics, using any of the pics attached. Use the attached pics, NO RANDOM STOCK PHOTOGRAPHY. For the color scheme of the graphics, they should all be complementary to the product colors or feel like Spring time.

Target Market(s)

primarily women

Requirements
Must have
• the photos and text attached

```html
<!DOCTYPE html>
<html lang="en">
<head>
<meta charset="utf-8">
<title>Spring Detox Sale – Social Graphics</title>
<link rel="stylesheet" href="https://fonts.googleapis.com/css2?family=Montserrat:ital,wght@0,500;0,700;0,800;0,900;1,500;1,700;1,800;1,900&family=Open+Sans:wght@700&display=swap">
<style>
  :root {
    --page: #ffffff;
    --green-deep: #0a6a0a;
    --green-mid: #2f9a14;
    --green-bright: #66cc0a;
    --lime: #9fe01a;
    --lime-text: #a6e312;
    --olive: #5f7f38;
    --olive-light: #8fb358;
    --ink: #151515;
    --white: #ffffff;
    --sun: #ffd600;
  }
  * { box-sizing: border-box; margin: 0; padding: 0; }
  html, body { width: 978px; height: 1200px; overflow: hidden; background: var(--page); }
  body { position: relative; font-family: "Montserrat", sans-serif; }

  .post { position: absolute; width: 450px; height: 562px; overflow: hidden; }
  .post--shine { left: 26px; top: 21px; background: linear-gradient(160deg, #1f8a1a 0%, var(--green-mid) 45%, #137a12 100%); }
  .post--circles { left: 498px; top: 21px; background: radial-gradient(circle at 50% 50%, #78e00c 0%, #4cba0c 35%, #1f8c0a 70%, var(--green-deep) 100%); }
  .post--refresh { left: 26px; top: 603px; background: linear-gradient(90deg, #6fcf08 0%, #3aa50b 45%, #0f7a0c 100%); }
  .post--reset { left: 498px; top: 603px; background: linear-gradient(180deg, #55703a 0%, #6f9346 55%, #8cb65a 100%); }

  .abs { position: absolute; }
  .photo { position: absolute; }

  /* Post 1 */
  .shine-line { position: absolute; inset: 0; }
  .shine-photo { left: 170px; top: 50px; width: 280px; height: 512px;
    background: linear-gradient(180deg, rgba(200,160,130,0.55) 0%, rgba(240,240,240,0.85) 45%, rgba(230,225,225,0.9) 80%, #e8e6e3 100%);
    border-radius: 120px 120px 0 0; }
  .shine-products { left: 95px; top: 420px; width: 355px; height: 142px;
    background: linear-gradient(180deg, rgba(245,245,245,0.95) 0%, #e2e0dd 100%); }
  .shine-price { left: 20px; top: 22px; font-weight: 800; font-size: 50px; color: var(--lime-text); letter-spacing: -1px; line-height: 1; }
  .shine-title { left: 20px; top: 87px; font-weight: 700; font-size: 20px; color: var(--white); }
  .shine-sub { left: 20px; top: 116px; font-weight: 500; font-style: italic; font-size: 18px; color: var(--white); }
  .shine-word { left: 18px; top: 164px; width: 64px; text-align: center; font-weight: 900; font-size: 66px; line-height: 62px; color: var(--white);
    text-shadow: 0 0 10px rgba(255,255,255,0.9), 0 0 22px rgba(200,255,160,0.8); }
  .shine-tag { left: 76px; top: 168px; font-weight: 900; font-style: italic; font-size: 23px; line-height: 25px; color: var(--white); }

  /* Post 2 */
  .rings { position: absolute; inset: 0; }
  .circ-price { left: 0; width: 100%; top: 200px; text-align: center; font-weight: 900; font-size: 64px; line-height: 1; letter-spacing: -2px;
    background: linear-gradient(180deg, #66cc0a 0%, #0c1a05 100%); -webkit-background-clip: text; background-clip: text; color: transparent; }
  .circ-label { left: 0; width: 100%; top: 270px; text-align: center; font-weight: 900; font-style: italic; font-size: 28px; color: var(--ink); }
  .circ-title { left: 0; width: 100%; top: 305px; text-align: center; font-family: "Open Sans", sans-serif; font-weight: 700; font-size: 42px; color: var(--white); }

  /* Post 3 */
  .ref-stripes { position: absolute; inset: 0; background: repeating-linear-gradient(90deg, rgba(255,255,255,0.03) 0 8px, rgba(0,0,0,0.03) 8px 22px); }
  .ref-price { left: 20px; top: 84px; font-weight: 900; font-size: 62px; line-height: 60px; color: var(--ink); letter-spacing: -2px;
    text-shadow: 4px 4px 10px rgba(0,0,0,0.25); }
  .ref-occasion { left: 20px; top: 222px; font-weight: 900; font-style: italic; font-size: 37px; color: var(--white); white-space: nowrap; letter-spacing: -0.5px; }
  .ref-head { left: 22px; top: 276px; font-weight: 900; font-size: 76px; line-height: 66px; letter-spacing: -1px;
    background: linear-gradient(180deg, #86ff10 0%, #b8f56a 45%, #ffffff 100%); -webkit-background-clip: text; background-clip: text; color: transparent; }

  /* Post 4 */
  .reset-photo { inset: 0; background: radial-gradient(ellipse at 72% 28%, rgba(150,180,100,0.6) 0%, rgba(90,120,60,0.3) 45%, transparent 70%); }
  .reset-bottles { left: 20px; top: 285px; width: 410px; height: 240px; border-radius: 14px 14px 8px 8px;
    background: linear-gradient(180deg, #f4f4f4 0%, #e9e6ea 70%, #d8cfe0 100%); }
  .reset-arc { position: absolute; inset: 0; }
  .reset-price { left: 20px; top: 36px; font-weight: 800; font-size: 64px; line-height: 70px; color: var(--lime-text); letter-spacing: -1px; }
  .reset-sale { left: 20px; top: 196px; font-weight: 700; font-style: italic; font-size: 24px; color: var(--lime-text); }
  .reset-sun { position: absolute; left: 250px; top: 220px; }
  .reset-tag { left: 19px; top: 237px; font-weight: 800; font-style: italic; font-size: 24.5px; color: var(--white); white-space: nowrap; }
</style>
</head>
<body>

<section class="post post--shine">
  <svg class="shine-line" width="450" height="562" viewBox="0 0 450 562" aria-hidden="true">
    <line x1="450" y1="0" x2="60" y2="365" stroke="#ffffff" stroke-width="2.5"/>
  </svg>
  <div class="photo shine-photo" role="img" aria-label="Smiling woman in a white cropped sweater gesturing toward the supplements"></div>
  <div class="photo shine-products" role="img" aria-label="Row of supplement bottles and cream tubes on a marble counter"></div>
  <div class="abs shine-price">25% Off</div>
  <div class="abs shine-title">Mother’s Day Sale:</div>
  <div class="abs shine-sub">Detox This Spring.</div>
  <div class="abs shine-word">S<br>H<br>I<br>N<br>E</div>
  <div class="abs shine-tag">THIS<br>SUMMER</div>
</section>

<section class="post post--circles">
  <svg class="rings" width="450" height="562" viewBox="0 0 450 562" aria-hidden="true">
    <circle cx="225" cy="278" r="195" fill="none" stroke="rgba(255,255,255,0.75)" stroke-width="2"/>
    <circle cx="225" cy="278" r="270" fill="none" stroke="rgba(255,255,255,0.35)" stroke-width="2"/>
  </svg>
  <div class="abs circ-price">25% Off</div>
  <div class="abs circ-label">ALL SUPPLEMENTS</div>
  <div class="abs circ-title">Spring Detox Sale!</div>
</section>

<section class="post post--refresh">
  <div class="ref-stripes" aria-hidden="true"></div>
  <div class="abs ref-price">25%<br>OFF</div>
  <div class="abs ref-occasion">Mother’s Day Sale</div>
  <div class="abs ref-head">REFRESH<br>YOUR<br>BODY</div>
</section>

<section class="post post--reset">
  <div class="photo reset-photo" role="img" aria-label="Smiling woman behind the supplements, tinted green"></div>
  <svg class="reset-arc" width="450" height="562" viewBox="0 0 450 562" aria-hidden="true">
    <path d="M 145 0 A 102 102 0 0 1 0 180" fill="none" stroke="#c8f04a" stroke-width="1.5"/>
  </svg>
  <div class="photo reset-bottles" role="img" aria-label="Four supplement bottles lined up in front"></div>
  <div class="abs reset-price">25%<br>Off</div>
  <div class="abs reset-sale">Spring Detox Sale</div>
  <svg class="reset-sun" width="80" height="30" viewBox="0 0 80 30" aria-hidden="true">
    <path d="M 24 24 A 20 20 0 0 1 64 24 Z" fill="var(--sun)"/>
    <line x1="0" y1="24" x2="80" y2="24" stroke="#b8e84a" stroke-width="1.5"/>
  </svg>
  <div class="abs reset-tag">Spring Reset. Summer Ready</div>
</section>

</body>
</html>
```